Webdesign für Kleingruppenreisen in die Südsteiermark
Zielgruppe
Wir sind ein Start-Up Unternehmen, das als Kleingruppenreisen in die Südsteiermark veranstaltet; der Schwerpunkt liegt auf dem Kulinarischen. Zielgruppe sind Geschäftsleute, die diese Kurzreisen (Do-So) für Marketingzwecke oder als Mitarbeiterbonus (oder auch privat) nutzen möchten.
Aufgabenstellung
Die Homepage soll eine Online-Shop Möglichkeit bieten, in der die Reise (bisher gibt es nur einen Ablauf) gebucht werden kann. Optisch sollte sie sich an das bereits von Ihnen erstellte Logo anlehnen und möglichst ansprechende Fotos von der Südsteiermark, Graz, Leoben usw. enthalten. (Siehe die beiden Flyer und das Logo)
Wir haben inzwischen Bildfreigaben von Haldauer und dem Tourismusverband Kellwinden erhalten und können auch eigene Bilder zur Verfügung stellen. Bitte kontaktieren Sie uns dafür, wenn nötig.

```html
<!DOCTYPE html>
<html lang="de">
<head>
<meta charset="utf-8">
<title>GaumenReisen – Kleingruppenreisen in die Südsteiermark</title>
<link href="https://fonts.googleapis.com/css2?family=Open+Sans:ital,wght@0,300;0,400;0,600;0,700;1,600&family=Kaushan+Script&display=swap" rel="stylesheet">
<style>
:root{
  --red:#a11d2b;
  --red-dark:#8e1622;
  --grey:#ebebeb;
  --text:#333;
  --white:#fff;
  --leaf:#8aa33a;
}
*{box-sizing:border-box;margin:0;padding:0}
html,body{width:1200px;height:2422px;overflow:hidden}
body{position:relative;font-family:"Open Sans",sans-serif;color:var(--text);background:var(--white)}
.abs{position:absolute}

/* Hero */
.hero{left:0;top:0;width:1200px;height:438px;background:linear-gradient(100deg,#3d5a1e 0%,#5d7c2a 30%,#a9b66a 55%,#d9dcd0 70%,#7f9a4a 85%,#4d6e24 100%);border-bottom:2px solid #ccc}
.brand{left:224px;top:0;width:244px;height:144px;background:var(--white);display:flex;align-items:center;justify-content:center}
.brand-name{font-family:"Open Sans",sans-serif;font-weight:700;font-size:30px;color:var(--red)}
.nav{left:468px;top:88px;width:502px;height:36px;background:var(--red);display:flex;align-items:center;padding-left:85px;gap:15px}
.nav a{color:var(--white);text-decoration:none;font-size:12px;font-weight:600}
.nav-leaf{left:920px;top:78px;width:100px;height:56px;border-radius:50%;background:radial-gradient(#8fb23a,#4f6a1c 70%,transparent 72%)}
.hero-caption{left:224px;background:var(--red);color:var(--white);font-size:23px;font-weight:600;padding:0 9px;height:50px;line-height:50px}
.dots{left:573px;top:423px;display:flex;gap:14px}
.dots span{width:7px;height:7px;background:#ccc}
.dots span.on{background:var(--red)}

/* Section headings */
.script{font-family:"Kaushan Script",cursive;color:var(--red);font-size:36px;text-align:center;width:1200px;left:0}
.divider{left:540px;width:120px;height:20px}
.lead{left:240px;width:720px;text-align:center;font-size:11.4px;line-height:13.6px;color:var(--text)}
.btn{background:var(--red);color:var(--white);font-size:15px;text-align:center;text-decoration:none;display:block}

/* Trips */
.trips{left:0;top:749px;width:1200px;height:418px;background:var(--grey)}
.card{width:220px;height:156px;box-shadow:0 0 3px rgba(0,0,0,.35);overflow:hidden}
.card-photo{width:100%;height:110px}
.card-label{position:absolute;left:0;bottom:0;width:100%;height:46px;background:rgba(161,29,43,.85);color:var(--white);font-size:19px;text-align:center;line-height:46px}
.card-text{width:220px;text-align:center;font-size:11.4px;line-height:13.6px}

/* CTA */
.cta{left:0;top:1167px;width:1200px;height:293px;background:linear-gradient(120deg,#b8434a,#a52a35 45%,#962230)}
.cta-title{left:229px;top:1204px;color:var(--white);font-style:italic;font-weight:600;font-size:30px;line-height:36px}
.cta-sub{left:229px;top:1314px;color:var(--white);font-weight:300;font-size:22px;line-height:27px}
.cta-btn{left:693px;top:1359px;width:287px;height:43px;border:1px solid var(--white);color:var(--white);font-style:italic;font-weight:600;font-size:22px;text-align:center;line-height:41px;text-decoration:none}

/* Gallery */
.tile{height:200px}
.promo{left:402px;top:1853px;width:400px;height:200px;background:linear-gradient(180deg,#b6423f,#a8302f 60%,#8f2424);color:var(--white);text-align:center}
.promo h3{font-weight:600;font-size:24px;margin-top:24px}
.promo p{font-size:11.4px;line-height:13.6px;width:340px;margin:6px auto 0}
.promo a{position:absolute;left:128px;top:152px;width:137px;height:29px;border:1px solid var(--white);color:var(--white);font-size:11.4px;line-height:27px;text-decoration:none}

/* Footer */
.footer{left:0;top:2218px;width:1200px;height:204px;background:var(--red);color:var(--white)}
.addr{left:246px;top:2251px;font-size:11px;line-height:13.5px}
.addr .fname{font-family:"Kaushan Script",cursive;font-size:13px}
.ficon{left:224px;width:12px;height:12px}
.fmenu{top:2251px;font-size:11px;line-height:22px}
.fmenu b{font-weight:700}
.social{top:2258px;width:52px;height:52px;border-radius:50%;background:var(--white)}
.frule{left:224px;top:2373px;width:750px;height:1px;background:rgba(255,255,255,.6)}
.copy{left:0;width:1200px;top:2385px;text-align:center;font-size:11px}
</style>
</head>
<body>

<header>
  <div class="abs hero" role="img" aria-label="Foto: Weinreben mit blauen Trauben vor sonnigen Weinbergen der Südsteiermark"></div>
  <div class="abs brand"><span class="brand-name">GaumenReisen</span></div>
  <nav class="abs nav">
    <a href="#">Startseite</a><a href="#">Jetzt buchen</a><a href="#">Shop</a><a href="#">Kontakt</a><a href="#">Ein Menüpunkt</a>
  </nav>
  <div class="abs nav-leaf" role="img" aria-label="Dekoratives Weinblatt"></div>
  <div class="abs hero-caption" style="top:270px">Lorem Ipsum dolor</div>
  <div class="abs hero-caption" style="top:331px;width:375px">consetetur sadipscing elitr, sed</div>
  <div class="abs dots"><span></span><span class="on"></span><span></span></div>
</header>

<section>
  <h2 class="abs script" style="top:466px">Herzlich Willkommen</h2>
  <svg class="abs divider" style="top:520px" viewBox="0 0 120 20" role="img" aria-label="Trennlinie mit Weinblatt"><line x1="0" y1="10" x2="50" y2="10" stroke="#555" stroke-width="1"/><line x1="70" y1="10" x2="120" y2="10" stroke="#555" stroke-width="1"/><circle cx="60" cy="10" r="8" fill="#8aa33a"/></svg>
  <p class="abs lead" style="top:558px">Wir lieben die Steiermark mit ihrem guten Essen, hervorragendem Bier und exquisitem Wein und möchten gerne anspruchsvolle Gäste verwöhnen. Als Start-up Unternehmen mit Sitz in Berlin und wollen wir unsere Begeisterung für die Steiermark mit ihren kulinarischen Spezialitäten, wunderschönen Landschaften und gastfreundlichen Menschen gern mit unseren Gästen teilen.<br>„GaumenReisen“ ist daher auf der Suche nach Partnern, die mit uns unser neues Projekt in der Steiermark starten möchten.</p>
  <a class="abs btn" href="#" style="left:528px;top:648px;width:138px;height:37px;line-height:37px">mehr Erfahren</a>
</section>

<section class="abs trips"></section>
<h2 class="abs script" style="top:757px">GaumenReisen</h2>
<svg class="abs divider" style="top:811px" viewBox="0 0 120 20" role="img" aria-label="Trennlinie mit Weinblatt"><line x1="0" y1="10" x2="50" y2="10" stroke="#555"/><line x1="70" y1="10" x2="120" y2="10" stroke="#555"/><circle cx="60" cy="10" r="8" fill="#8aa33a"/></svg>

<div class="abs card" style="left:223px;top:852px"><div class="card-photo" role="img" aria-label="Foto: Weinberg mit Hügeln unter blauem Himmel" style="background:linear-gradient(#8db4dc,#c6d6e4 45%,#5f7a3a 60%,#4a5f2a)"></div><div class="card-label">Vom Bier zum Wein</div></div>
<div class="abs card" style="left:489px;top:848px"><div class="card-photo" role="img" aria-label="Foto: Weinberg unter Wolkenhimmel" style="background:linear-gradient(#4f8ad0,#e6eef6 40%,#6b7f45 62%,#4a5f2a)"></div><div class="card-label">lorem Ipsum</div></div>
<div class="abs card" style="left:756px;top:852px"><div class="card-photo" role="img" aria-label="Foto: Bergsee mit Felswänden" style="background:linear-gradient(#3e78b8,#7a8f8a 35%,#4e8a9a 60%,#8ec6d0)"></div><div class="card-label">lorem Ipsum</div></div>

<p class="abs card-text" style="left:223px;top:1022px">Lernen Sie Leoben, die Hauptstadt des Haldauer-Bieres kennen  und erfahren Sie im Haldeum die Geschichte dieses weltbekannten Gebräus.</p>
<p class="abs card-text" style="left:489px;top:1022px">Lorem ipsum dolor sit amet, consetetur sadipscing elitr, sed diam nonumy eirmod tempor invidunta.</p>
<p class="abs card-text" style="left:756px;top:1022px">Lorem ipsum dolor sit amet, consetetur sadipscing elitr, sed diam nonumy eirmod tempor invidunta.</p>

<a class="abs btn" href="#" style="left:264px;top:1090px;width:138px;height:37px;line-height:37px">mehr Erfahren</a>
<a class="abs btn" href="#" style="left:531px;top:1090px;width:137px;height:37px;line-height:37px">mehr Erfahren</a>
<a class="abs btn" href="#" style="left:796px;top:1090px;width:138px;height:37px;line-height:37px">mehr Erfahren</a>

<section class="abs cta" role="img" aria-label="Hintergrundfoto: Weintrauben, rot eingefärbt"></section>
<h2 class="abs cta-title">Erleben Sie die<br>gastronomische Vielfalt der Süd-Steiermark</h2>
<p class="abs cta-sub">Sie suchen ein bestimmtes Gaumenerlebnis?<br>Dann helfen wir Ihnen gerne weiter.</p>
<a class="abs cta-btn" href="#">Jetzt beraten lassen</a>

<section>
  <h2 class="abs script" style="top:1476px">Unsere Angebote</h2>
  <svg class="abs divider" style="top:1529px" viewBox="0 0 120 20" role="img" aria-label="Trennlinie mit Weinblatt"><line x1="0" y1="10" x2="50" y2="10" stroke="#555"/><line x1="70" y1="10" x2="120" y2="10" stroke="#555"/><circle cx="60" cy="10" r="8" fill="#8aa33a"/></svg>
  <p class="abs lead" style="top:1566px">Unser Ziel ist es, exklusive Klein-gruppenreisen mit kulinarischem Schwerpunkt in die Steiermark zu führen. Wir konzentrieren uns auf Geschäftsleute aus Berlin und Brandenburg, die unsere Reisen als Marketinginstrument für Kunden, im Rahmen der Wertschätzung von Mitarbeitern oder auch einfach nur privat nutzen möchten.</p>
</section>

<div class="abs tile" style="left:0;top:1642px;width:179px;background:linear-gradient(#4a4a40,#b8c060 50%,#3a3a34)" role="img" aria-label="Foto: Braukessel in einem Museum"></div>
<div class="abs tile" style="left:189px;top:1642px;width:200px;background:linear-gradient(#2f7fd0,#7ab2e8 55%,#a0472e 70%,#5c7a36)" role="img" aria-label="Foto: Klapotetz über einem Bauernhaus"></div>
<div class="abs tile" style="left:402px;top:1642px;width:199px;background:linear-gradient(#4e8ad0,#d06a40 45%,#c9a070 75%,#555)" role="img" aria-label="Foto: Altstadt von Graz mit Uhrturm"></div>
<div class="abs tile" style="left:614px;top:1642px;width:200px;background:linear-gradient(90deg,#5c95d6,#e0c070 40%,#d8b85e 60%,#2f3a26)" role="img" aria-label="Foto: gelber Kirchturm"></div>
<div class="abs tile" style="left:824px;top:1642px;width:200px;background:radial-gradient(#5a5470,#2a2a3a 70%,#4a5a2a)" role="img" aria-label="Foto: blaue Weintrauben"></div>
<div class="abs tile" style="left:1037px;top:1642px;width:163px;background:linear-gradient(#6a9ad0,#c8d8e6 50%,#7aa040 75%,#4a6a3a)" role="img" aria-label="Foto: Bergwiese mit See"></div>

<div class="abs tile" style="left:0;top:1853px;width:389px;background:linear-gradient(#8aa0b6,#9aa0a0 35%,#3a5a2a 60%,#6a8a3a)" role="img" aria-label="Foto: Wanderer vor Dachsteinmassiv"></div>
<div class="abs promo">
  <h3>Eine coole Headline</h3>
  <p>Lorem ipsum dolor sit amet, consetetur sadipscing elitr, sed diam nonumy eirmod tempor invidunt ut labore et dolore magna aliquyam erat, sed diam voluptua.</p>
  <a href="#">Jetzt mehr erfahren</a>
</div>
<div class="abs tile" style="left:827px;top:1853px;width:373px;background:linear-gradient(#9ab0c0,#e8c890 35%,#6a7a3a 60%,#3a5220)" role="img" aria-label="Foto: Klapotetz bei Sonnenuntergang über Weinbergen"></div>

<footer>
  <svg class="abs" style="left:0;top:2094px" width="560" height="128" viewBox="0 0 560 128" role="img" aria-label="Silhouette von Bergen und Ortschaft"><path d="M0 128 L0 80 C40 60 80 40 130 30 C170 10 220 0 260 20 C300 40 360 60 420 80 C480 100 530 110 560 128 Z" fill="#a11d2b"/></svg>
  <div class="abs footer"></div>
  <svg class="abs ficon" style="top:2253px" viewBox="0 0 12 12" role="img" aria-label="Standort"><path d="M6 0a4 4 0 0 0-4 4c0 3 4 8 4 8s4-5 4-8a4 4 0 0 0-4-4zm0 5.5a1.5 1.5 0 1 1 0-3 1.5 1.5 0 0 1 0 3z" fill="#fff"/></svg>
  <div class="abs addr"><span class="fname">GaumenReisen</span><br>Marlene Hoffbauer<br>Lindenweg 12<br>D - 10115 Berlin<br><br>Deutschland: +49 170 0000 123<br>Österreich: +43 681 0000 4567</div>
  <svg class="abs ficon" style="top:2318px" viewBox="0 0 12 12" role="img" aria-label="Telefon"><path d="M2.5 0.5l2 2.5-1.2 1.2c.6 1.4 1.8 2.6 3.3 3.3L7.8 6.3l2.5 2-1 2.5C5 10.8 1.2 7 1 2.2z" fill="#fff"/></svg>
  <div class="abs fmenu" style="left:459px"><b>MENÜ</b><br>MENÜPUNKT<br>MENÜPUNKT<br>MENÜPUNKT<br>MENÜPUNKT</div>
  <div class="abs fmenu" style="left:598px"><b>MENÜ</b><br>MENÜPUNKT<br>MENÜPUNKT<br>MENÜPUNKT<br>MENÜPUNKT</div>
  <a class="abs social" href="#" style="left:737px" aria-label="Soziales Netzwerk 1"></a>
  <a class="abs social" href="#" style="left:800px" aria-label="Videoplattform"></a>
  <a class="abs social" href="#" style="left:862px" aria-label="Soziales Netzwerk 2"></a>
  <a class="abs social" href="#" style="left:925px" aria-label="Kurznachrichtendienst"></a>
  <div class="abs frule"></div>
  <p class="abs copy">© 2017. Agentur Brinkmann</p>
</footer>

</body>
</html>
```